New LLC consulting company needs a business card design

I need a business card design for new company in Alexandria Virginia called TK Verdane Consulting LLC. The company is focused on consulting for defense and national security issues with expertise in nuclear and space topics. I would like to see designs that are simple and I am open to colors except for brown.

Target Market(s)

All businesses that are seeking consulting help

Industry/Entity Type

Consulting

Contact Information for Business Card

Name of company - TK Verdane Consulting LLC; name (Delia Pratt) President; email: prattdq47@mailvessa.com; Phone: 703-555-0142

Requirements
Must have
• The details described above
Nice to have
• I'm open to all ideas
Should not have
• No brown

```html
<!DOCTYPE html>
<html lang="en">
<head>
<meta charset="utf-8">
<title>TK Verdane Consulting LLC — Business Card</title>
<link rel="stylesheet" href="https://fonts.googleapis.com/css2?family=Montserrat:wght@300;400;500;600;700&display=swap">
<style>
  :root {
    --bg: #c4c4c4;
    --card-red: #ae0014;
    --card-red-deep: #8a000f;
    --brand-red: #b5000f;
    --ink: #111111;
    --paper: #ffffff;
  }
  * { margin: 0; padding: 0; box-sizing: border-box; }
  html, body {
    width: 1200px;
    height: 1015px;
    overflow: hidden;
    background: var(--bg);
    font-family: "Montserrat", sans-serif;
  }
  .sheet {
    position: relative;
    width: 1200px;
    height: 1015px;
  }
  .card {
    position: absolute;
    left: 320px;
    width: 560px;
    height: 320px;
    overflow: hidden;
    box-shadow: 0 6px 16px rgba(0,0,0,0.25);
  }
  .card--back {
    top: 150px;
    background: var(--card-red);
    display: flex;
    align-items: center;
    justify-content: center;
  }
  .card--front {
    top: 545px;
    background: var(--paper);
  }
  .brand {
    font-weight: 500;
    text-transform: uppercase;
    line-height: 1.05;
  }
  .brand__line { display: block; }
  .brand__line--main { font-size: 38px; letter-spacing: 0.5px; }
  .brand__line--sub { font-size: 30px; letter-spacing: 0.5px; }

  .card--back .brand { color: var(--card-red-deep); }

  .card--front .brand {
    position: absolute;
    right: 38px;
    top: 62px;
    color: var(--brand-red);
    text-align: left;
  }
  .card--front .brand__line--main { font-size: 32px; }
  .card--front .brand__line--sub { font-size: 26px; }

  .split {
    position: absolute;
    inset: 0;
  }
  .contact {
    position: absolute;
    left: 36px;
    top: 200px;
    color: var(--paper);
  }
  .contact__name {
    font-size: 24px;
    font-weight: 700;
    text-transform: uppercase;
    letter-spacing: 0.5px;
    line-height: 1;
  }
  .contact__role {
    font-size: 14px;
    font-weight: 400;
    margin-top: 2px;
  }
  .contact__list {
    list-style: none;
    margin-top: 22px;
    font-size: 15px;
    font-weight: 400;
  }
  .contact__item {
    display: flex;
    align-items: center;
    gap: 8px;
    line-height: 1.5;
  }
  .contact__icon { width: 13px; height: 13px; flex: none; }
</style>
</head>
<body>
<main class="sheet">
  <section class="card card--back" aria-label="Card back">
    <p class="brand">
      <span class="brand__line brand__line--main">TK Verdane</span>
      <span class="brand__line brand__line--sub">Consulting LLC</span>
    </p>
  </section>

  <section class="card card--front" aria-label="Card front">
    <svg class="split" width="560" height="320" viewBox="0 0 560 320" aria-hidden="true">
      <polygon points="0,0 150,0 336,320 0,320" fill="var(--card-red)"/>
      <line x1="150" y1="0" x2="336" y2="320" stroke="var(--ink)" stroke-width="3"/>
      <line x1="162" y1="0" x2="268" y2="182" stroke="var(--ink)" stroke-width="2"/>
      <line x1="268" y1="182" x2="300" y2="190" stroke="var(--ink)" stroke-width="2"/>
    </svg>

    <p class="brand">
      <span class="brand__line brand__line--main">TK Verdane</span>
      <span class="brand__line brand__line--sub">Consulting LLC</span>
    </p>

    <div class="contact">
      <h1 class="contact__name">Delia Pratt</h1>
      <p class="contact__role">President</p>
      <ul class="contact__list">
        <li class="contact__item">
          <svg class="contact__icon" viewBox="0 0 24 24" aria-hidden="true"><path fill="#fff" d="M6.6 10.8a15.1 15.1 0 0 0 6.6 6.6l2.2-2.2a1 1 0 0 1 1-.25 11.4 11.4 0 0 0 3.6.57 1 1 0 0 1 1 1V20a1 1 0 0 1-1 1A17 17 0 0 1 3 4a1 1 0 0 1 1-1h3.5a1 1 0 0 1 1 1c0 1.25.2 2.45.57 3.57a1 1 0 0 1-.25 1z"/></svg>
          <span>703-555-0142</span>
        </li>
        <li class="contact__item">
          <svg class="contact__icon" viewBox="0 0 24 24" aria-hidden="true"><path fill="#fff" d="M2 5h20v14H2z"/><path d="M2 5l10 8 10-8" fill="none" stroke="var(--card-red)" stroke-width="2"/></svg>
          <span>prattdq47@mailvessa.com</span>
        </li>
      </ul>
    </div>
  </section>
</main>
</body>
</html>
```